Varentoria Business Card and Letter Head

We are a leadership assessment consultancy based in Harbourvale, Australia. We help executive-level decison-makers select leaders for more senior level roles in corporate and government organisations. Our methodology is based on the latest research from the field of neuroscience.
We need a business card design and matching letter head that presents our company, Varentoria, as a:
1. trusted adviser to senior executive-level decison makers
2. niche consultancy who are experts in the field of assessing leadership talent
3. results-focused solution provider who balance scientific methods with pragmatic solutions
The following company details should be used in all designs:
Company Name: Varentoria
Details (for business card):
Derek Hanford
Prime Capacity Officer
Level 14, Marlow Tower
7 Marlow Square
Harbourvale, NSW 2160 Australia
Phone: 1300 582 714
Mobile: 0412 637 258
Email: derek.hanford@varentoria-example.com.au
Website: varentoria-example.com.au
I have attached the logo for Varentoria (for both a white and black background) - your business card and letter head designs must incoporate this logo and colour scheme.
Thanks for your interest in this project, I'm looking forward to receiving your ideas.
Regards,
Derek
Target Market(s)
Executive-level decison-makers in corporate and government organisations (e.g., CEO, VP, Head of Human Resources)
Industry/Entity Type
Leadership
Look and feel

```html
<!DOCTYPE html>
<html lang="en">
<head>
<meta charset="utf-8">
<title>Varentoria Stationery</title>
<link rel="stylesheet" href="https://fonts.googleapis.com/css2?family=Montserrat:wght@700&family=Questrial&display=swap">
<style>
  :root {
    --red: #c0341d;
    --red-soft: rgba(192, 52, 29, 0);
    --ink: #3d3d3f;
    --grey: #8a8a8c;
    --frame: #b9b9bb;
    --paper: #ffffff;
    --dark: #48484b;
    --dark-centre: #8b8b8e;
    --backdrop: #efe9e2;
    --pale: #d9d9db;
  }
  * { box-sizing: border-box; margin: 0; padding: 0; }
  html, body { width: 1200px; height: 834px; overflow: hidden; }
  body {
    position: relative;
    background: var(--backdrop);
    font-family: "Questrial", Arial, sans-serif;
    color: var(--ink);
  }
  .piece { position: absolute; }

  /* logo lockup */
  .logo { display: flex; align-items: center; gap: 8px; }
  .logo-mark { width: var(--mark, 30px); height: var(--mark, 30px); background: var(--red); flex: none; }
  .logo-name { font-family: "Montserrat", Arial, sans-serif; font-weight: 700; font-size: var(--name, 26px); line-height: 1; color: var(--ink); letter-spacing: -0.5px; white-space: nowrap; }
  .logo-tagline { font-size: var(--tag, 8px); letter-spacing: 0.3px; color: var(--grey); text-transform: uppercase; margin-top: 3px; white-space: nowrap; }
  .logo.on-dark .logo-name { color: var(--pale); }
  .on-dark-tagline { color: #b3b3b5; }

  .red-band { position: absolute; height: 9px; background: linear-gradient(90deg, var(--red), var(--red-soft)); }

  /* letterhead */
  .letterhead { left: 23px; top: 37px; width: 539px; height: 762px; background: var(--paper); box-shadow: 0 2px 8px rgba(0,0,0,.18); }
  .letterhead-frame { position: absolute; left: 9px; top: 11px; right: 9px; bottom: 39px; border: 2px solid var(--frame); }
  .letterhead .logo-block { position: absolute; left: 25px; top: 28px; --mark: 36px; --name: 28px; --tag: 8px; }
  .letterhead .red-band { left: 11px; right: 11px; top: 90px; }
  .footer-line { position: absolute; font-size: 8px; color: var(--ink); white-space: nowrap; }
  .footer-line .label { color: var(--grey); }
  .letterhead .footer-line { left: 12px; bottom: 18px; }

  /* business card back */
  .card-back {
    left: 87px; top: 258px; width: 315px; height: 170px; padding: 10px;
    background: linear-gradient(200deg, var(--red), #8a4a44 70%, var(--grey));
    box-shadow: 0 3px 8px rgba(0,0,0,.3);
  }
  .card-back-face { width: 100%; height: 100%; background: radial-gradient(circle at 50% 45%, var(--dark-centre), var(--dark) 70%); display: flex; align-items: center; justify-content: center; }
  .logo-box { border: 1px solid #a9a9ab; padding: 10px 14px; --mark: 30px; --name: 24px; --tag: 7px; }

  /* business card front */
  .card-front { left: 184px; top: 440px; width: 315px; height: 170px; background: var(--paper); box-shadow: 0 3px 8px rgba(0,0,0,.25); }
  .card-front-frame { position: absolute; inset: 8px; border: 1.5px solid var(--frame); }
  .card-front .logo-mark { position: absolute; left: 20px; top: 20px; width: 26px; height: 26px; background: var(--red); }
  .card-name { position: absolute; left: 56px; top: 16px; font-family: "Montserrat", Arial, sans-serif; font-weight: 700; font-size: 15px; color: var(--red); }
  .card-title { position: absolute; left: 56px; top: 35px; font-size: 12px; color: var(--ink); }
  .card-front .red-band { left: 10px; right: 10px; top: 54px; height: 6px; }
  .contact-list { position: absolute; left: 104px; top: 70px; list-style: none; font-size: 8.5px; line-height: 1.25; white-space: nowrap; }
  .contact-list li { display: flex; align-items: flex-start; gap: 7px; margin-bottom: 3px; }
  .contact-list svg { width: 9px; height: 9px; flex: none; margin-top: 1px; fill: none; stroke: var(--grey); stroke-width: 1.2; }

  /* envelope */
  .envelope { left: 576px; top: 60px; width: 601px; height: 374px; }
  .envelope-flap { position: absolute; left: 0; top: 0; width: 601px; height: 112px; }
  .envelope-flap .logo-box { position: absolute; left: 236px; top: 40px; padding: 6px 10px; --mark: 18px; --name: 15px; --tag: 5px; opacity: .55; }
  .envelope-body { position: absolute; left: 0; top: 112px; width: 601px; height: 262px; background: var(--paper); box-shadow: 0 2px 8px rgba(0,0,0,.18); }
  .envelope-frame { position: absolute; left: 7px; top: 6px; right: 7px; bottom: 36px; border: 1.5px solid var(--frame); }
  .envelope .logo-block { position: absolute; left: 22px; top: 24px; --mark: 28px; --name: 20px; --tag: 6px; }
  .envelope .red-band { left: 8px; right: 8px; top: 69px; height: 8px; }
  .envelope .footer-line { left: 18px; bottom: 16px; font-size: 7.5px; }

  /* disc */
  .disc { left: 885px; top: 474px; width: 318px; height: 318px; }

  /* disc case */
  .disc-case {
    left: 595px; top: 473px; width: 322px; height: 322px; padding: 12px;
    background: linear-gradient(25deg, var(--grey), #a94a3c 55%, var(--red));
    box-shadow: 0 3px 8px rgba(0,0,0,.3);
  }
  .disc-case-face { width: 100%; height: 100%; background: radial-gradient(circle at 50% 45%, var(--dark-centre), var(--dark) 72%); display: flex; flex-direction: column; align-items: center; justify-content: center; gap: 16px; }
  .disc-case .logo-box { --mark: 26px; --name: 20px; --tag: 6px; padding: 8px 12px; margin-top: -30px; }
  .disc-title { font-size: 18px; color: #b8b8ba; letter-spacing: .5px; }
</style>
</head>
<body>

<section class="piece letterhead">
  <div class="letterhead-frame"></div>
  <div class="logo-block">
    <div class="logo"><span class="logo-mark"></span><span class="logo-name">Varentoria</span></div>
    <div class="logo-tagline">Assessing Leadership Depth</div>
  </div>
  <div class="red-band"></div>
  <p class="footer-line"><span class="label">Office:</span> Level 14, Marlow Tower, 7 Marlow Square Harbourvale, NSW 2160 Australia &nbsp;&nbsp;&nbsp; <span class="label">Phone:</span> 1300 582 714 &nbsp;&nbsp;&nbsp; <span class="label">Website:</span> varentoria-example.com.au</p>
</section>

<section class="piece card-back">
  <div class="card-back-face">
    <div class="logo-box">
      <div class="logo on-dark"><span class="logo-mark"></span><span class="logo-name">Varentoria</span></div>
      <div class="logo-tagline on-dark-tagline">Assessing Leadership Depth</div>
    </div>
  </div>
</section>

<section class="piece card-front">
  <div class="card-front-frame"></div>
  <span class="logo-mark"></span>
  <h1 class="card-name">Derek Hanford</h1>
  <p class="card-title">Prime Capacity Officer</p>
  <div class="red-band"></div>
  <ul class="contact-list">
    <li><svg viewBox="0 0 10 10"><rect x="2" y="1" width="6" height="8"/><path d="M4 3h2M4 5h2M4 7h2"/></svg><span>Level 14, Marlow Tower 7 Marlow Square<br>Harbourvale NSW 2160 Australia</span></li>
    <li><svg viewBox="0 0 10 10"><path d="M2 1l2 0 1 2-1 1q1 2 3 3l1-1 2 1 0 2q-5 0-8-8z"/></svg><span>1300 582 714</span></li>
    <li><svg viewBox="0 0 10 10"><rect x="3" y="1" width="4" height="8" rx=".6"/><path d="M4.5 7.5h1"/></svg><span>0412 637 258</span></li>
    <li><svg viewBox="0 0 10 10"><rect x="1" y="2.5" width="8" height="5"/><path d="M1 2.5l4 3 4-3"/></svg><span>derek.hanford@varentoria-example.com.au</span></li>
    <li><svg viewBox="0 0 10 10"><circle cx="5" cy="5" r="4"/><path d="M1 5h8M5 1q-2 4 0 8M5 1q2 4 0 8"/></svg><span>varentoria-example.com.au</span></li>
  </ul>
</section>

<section class="piece envelope">
  <div class="envelope-flap">
    <svg width="601" height="112" viewBox="0 0 601 112" aria-hidden="true">
      <defs>
        <radialGradient id="flap-shade" cx="0.45" cy="0.5" r="0.6">
          <stop offset="0" stop-color="#a5a5a8"/>
          <stop offset="1" stop-color="#48484b"/>
        </radialGradient>
      </defs>
      <path d="M0 112 L40 40 Q300 -20 560 40 L601 112 Z" fill="url(#flap-shade)"/>
    </svg>
    <div class="logo-box">
      <div class="logo on-dark"><span class="logo-mark"></span><span class="logo-name">Varentoria</span></div>
    </div>
  </div>
  <div class="envelope-body">
    <div class="envelope-frame"></div>
    <div class="logo-block">
      <div class="logo"><span class="logo-mark"></span><span class="logo-name">Varentoria</span></div>
      <div class="logo-tagline">Assessing Leadership Depth</div>
    </div>
    <div class="red-band"></div>
    <p class="footer-line"><span class="label">Office:</span> Level 14, Marlow Tower, 7 Marlow Square Harbourvale, NSW 2160 Australia &nbsp;<span class="label">Phone:</span> 1300 582 714 &nbsp;<span class="label">Mobile:</span> 0412 637 258 &nbsp;<span class="label">Website:</span> varentoria-example.com.au</p>
  </div>
</section>

<svg class="piece disc" viewBox="0 0 318 318" aria-hidden="true">
  <defs>
    <linearGradient id="disc-arc" x1="0" y1="0" x2="1" y2="1">
      <stop offset="0" stop-color="#c0341d"/>
      <stop offset="1" stop-color="#c0341d" stop-opacity="0"/>
    </linearGradient>
    <path id="disc-title-path" d="M25 195 A138 138 0 0 0 293 195"/>
  </defs>
  <circle cx="159" cy="159" r="155" fill="#ffffff" stroke="#d4d4d6" stroke-width="5"/>
  <path d="M20 170 A142 142 0 0 1 298 150" fill="none" stroke="url(#disc-arc)" stroke-width="4"/>
  <rect x="58" y="74" width="20" height="20" fill="#c0341d"/>
  <text x="85" y="92" font-family="Montserrat, Arial, sans-serif" font-weight="700" font-size="20" fill="#3d3d3f">Varentoria</text>
  <text x="86" y="104" font-family="Questrial, Arial, sans-serif" font-size="6" fill="#8a8a8c">ASSESSING LEADERSHIP DEPTH</text>
  <circle cx="150" cy="162" r="34" fill="#efe9e2" stroke="#d4d4d6" stroke-width="2"/>
  <text font-family="Questrial, Arial, sans-serif" font-size="17" fill="#c0341d"><textPath href="#disc-title-path" startOffset="27%">Your Title Here</textPath></text>
</svg>

<section class="piece disc-case">
  <div class="disc-case-face">
    <div class="logo-box">
      <div class="logo on-dark"><span class="logo-mark"></span><span class="logo-name">Varentoria</span></div>
      <div class="logo-tagline on-dark-tagline">Assessing Leadership Depth</div>
    </div>
    <p class="disc-title">Your Title Here</p>
  </div>
</section>

</body>
</html>
```